NEW Modern Sleek Business Card for VR Language Startup

Our startup is using VR to lead the next wave of world language education. We need a two-sided business card that introduces the larger organization (Tessavane Language Inc) and our contact info on one side and shows the product, Glimwoorld, on the other side.

Side 1 (contact info)= Tessavane Logo and Contact info (name, title, phone, email)

Side 2 (product)= Glimworld logo, text, and website
Text= Culturally Immersive Language Learning Games
Website= www.glimworld-play.com

Target Market(s)

Education, Technology

Contact Information for Business Card

Contact info will be updated upon approval of the design. For now, put this as a placeholder.

Perry Dunmore
Founder & CEO
pdunmore@quillpost-mail.net
(555)-014-2286

Font styles to use
Other font styles liked:
• Gibson and Century Gothic are the brand fonts

Requirements
Nice to have
• I would love to see cohesion between the design and colors of the two logos. I have attached a few business card designs that I like, so you can get a feel for my preferred style.

```html
<!DOCTYPE html>
<html lang="en">
<head>
<meta charset="utf-8">
<title>Tessavane Language Inc – Business Card</title>
<link href="https://fonts.googleapis.com/css2?family=Lato:wght@400;700&display=swap" rel="stylesheet">
<style>
  :root {
    --page: #d6d6d6;
    --card-light: #ffffff;
    --card-dark: #4d4d4d;
    --ink: #1e1e1e;
    --rule-dark: #2a2a2a;
    --rule-light: #bdbdbd;
    --white: #ffffff;
    --cyan: #2cc8e8;
    --accent-purple: #7b5af0;
    --g-yellow: #f1c93b;
    --g-orange: #f2713a;
    --g-magenta: #c24aa0;
    --g-purple: #7b5af0;
    --g-blue: #4fa3f5;
    --g-cyan: #16f0e0;
  }
  * { box-sizing: border-box; margin: 0; padding: 0; }
  html, body { width: 1200px; height: 802px; overflow: hidden; }
  body {
    background: var(--page);
    font-family: "Lato", "Century Gothic", sans-serif;
    position: relative;
  }
  .card {
    position: absolute;
    top: 274px;
    width: 442px;
    height: 265px;
    overflow: hidden;
    box-shadow: 0 3px 8px rgba(0,0,0,0.25);
  }
  .card--contact { left: 136px; background: var(--card-light); }
  .card--product { left: 624px; background: var(--card-dark); }

  .numeral-art {
    position: absolute;
    top: 0;
    left: 0;
    height: 265px;
    border-radius: 0 130px 130px 0 / 0 132px 132px 0;
    background: linear-gradient(180deg,
      var(--g-yellow) 0%, var(--g-orange) 22%, var(--g-magenta) 45%,
      var(--g-purple) 65%, var(--g-blue) 82%, var(--g-cyan) 100%);
  }
  .card--contact .numeral-art { width: 165px; }
  .card--product .numeral-art { width: 185px; }

  .brand {
    position: absolute;
    right: 37px;
    display: flex;
    align-items: center;
    gap: 10px;
  }
  .brand__dot { width: 26px; height: 26px; border-radius: 50%; flex: none; }
  .brand__name { font-weight: 700; font-size: 26px; line-height: 1; white-space: nowrap; }

  .card--contact .brand { top: 68px; }
  .card--contact .brand__dot { background: var(--accent-purple); }
  .card--contact .brand__name { color: var(--ink); letter-spacing: 2.5px; text-transform: uppercase; font-size: 24px; }

  .card--product .brand { top: 100px; right: 35px; }
  .card--product .brand__dot { background: var(--g-blue); }
  .card--product .brand__name { color: var(--white); font-weight: 400; }

  .divider { position: absolute; top: 140px; height: 1px; }
  .card--contact .divider { left: 176px; width: 229px; background: var(--rule-dark); }
  .card--product .divider { left: 196px; width: 218px; background: var(--rule-light); }

  .contact {
    position: absolute;
    right: 37px;
    top: 164px;
    text-align: right;
    color: var(--ink);
  }
  .contact__name { font-weight: 700; font-size: 17px; line-height: 18px; text-transform: uppercase; }
  .contact__title { font-size: 12.5px; line-height: 14px; }
  .contact__lines { margin-top: 12px; font-size: 12.5px; line-height: 17px; }
  .contact__line { display: flex; justify-content: flex-end; align-items: center; gap: 4px; }
  .contact__line svg { width: 11px; height: 11px; fill: var(--ink); }

  .tagline {
    position: absolute;
    right: 27px;
    top: 173px;
    text-align: right;
    color: var(--white);
    font-size: 12.5px;
    line-height: 16px;
    text-transform: uppercase;
  }
  .website {
    position: absolute;
    right: 27px;
    top: 219px;
    color: var(--cyan);
    font-size: 14px;
    letter-spacing: 1.2px;
  }
</style>
</head>
<body>
  <section class="card card--contact">
    <div class="numeral-art" role="img" aria-label="Large rainbow gradient numeral decoration bleeding off the left edge"></div>
    <div class="brand">
      <span class="brand__dot"></span>
      <span class="brand__name">Tessavane</span>
    </div>
    <div class="divider"></div>
    <div class="contact">
      <p class="contact__name">Perry Dunmore</p>
      <p class="contact__title">Founder &amp; CEO</p>
      <div class="contact__lines">
        <p class="contact__line">(555)-014-2286
          <svg viewBox="0 0 12 12" aria-hidden="true"><path d="M1 4c0-2 2-3 5-3s5 1 5 3l-2 1-1-2H4L3 5zM3 6h6l2 5H1z"/></svg>
        </p>
        <p class="contact__line">pdunmore@quillpost-mail.net
          <svg viewBox="0 0 12 12" aria-hidden="true"><path d="M1 2h10v8H1zM2 3v1l4 3 4-3V3L6 6z"/></svg>
        </p>
      </div>
    </div>
  </section>

  <section class="card card--product">
    <div class="numeral-art" role="img" aria-label="Large rainbow gradient numeral decoration bleeding off the left edge"></div>
    <div class="brand">
      <span class="brand__dot"></span>
      <span class="brand__name">Glimworld</span>
    </div>
    <div class="divider"></div>
    <p class="tagline">Culturally Immersive<br>Language Learning Games</p>
    <p class="website">www.glimworld-play.com</p>
  </section>
</body>
</html>
```